Harbourline Electrical Solutions

On one side. LOGO (underneath:) Commercial Industrial Residential

- NAME & CONTACT DETAILS

Marcus T. Hollings
Project Manager

(Cell icon) (441) 555-0187
(Email icon) hlelectricalsolutions@mailvento.com
(Facebook & Instagram icons )@hlelectricalsolutions

Other side: LOGO - underneath ELECTRICAL CONSTRUCTION & MAINTENANCE . LED LIGHTING & AUTOMATION . LIFE SAFETY SYSTEMS (FIRE ALARM / SECURITY) . DATA & COMMUNICATION

```html
<!DOCTYPE html>
<html lang="en">
<head>
<meta charset="utf-8">
<title>Harbourline Electrical Solutions – Business Card</title>
<link href="https://fonts.googleapis.com/css2?family=Montserrat:wght@300;400;500;700&display=swap" rel="stylesheet">
<style>
  :root{
    --bg:#262628;
    --teal:#10576c;
    --teal-deep:#0c4a5c;
    --teal-band:#1f6478;
    --ink:#1c1c1e;
    --grey:#4a4a4a;
    --white:#ffffff;
  }
  *{box-sizing:border-box;margin:0;padding:0}
  html,body{width:1200px;height:1200px;overflow:hidden}
  body{background:var(--bg);font-family:"Montserrat",Arial,sans-serif;position:relative}

  .card{position:absolute}
  .card--front{left:286px;top:217px;width:612px;height:368px;background:var(--teal)}
  .card--back{left:292px;top:632px;width:600px;height:360px;background:var(--white)}

  .wordmark{position:absolute;left:0;right:0;text-align:center;text-transform:uppercase;font-weight:500;line-height:1.15}
  .card--front .wordmark{top:132px;color:var(--teal-deep);font-size:26px;letter-spacing:4px}
  .card--back .wordmark{top:38px;color:var(--teal);font-size:26px;letter-spacing:4px}
  .wordmark span{display:block}
  .wordmark .sub{font-size:18px;letter-spacing:5px}

  .services{position:absolute;left:0;right:0;top:310px;text-align:center;color:var(--white);font-weight:300;font-size:12.2px;line-height:17px;letter-spacing:.1px}

  .sectors{position:absolute;left:0;right:0;top:123px;text-align:center;font-size:11.5px;font-weight:500;letter-spacing:3px;color:var(--ink)}
  .sectors .sep{color:var(--teal);margin:0 6px}

  .person{position:absolute;right:313px;top:280px;text-align:right;white-space:nowrap}
  .person__name{font-size:15.5px;font-weight:700;color:var(--teal);letter-spacing:.2px;text-transform:uppercase;line-height:20px}
  .person__role{font-size:11px;font-weight:500;color:var(--ink);line-height:14px}
  .divider{position:absolute;left:299px;top:268px;width:1.5px;height:54px;background:var(--teal)}

  .contacts{position:absolute;left:310px;top:272px;list-style:none;font-size:11.5px;color:var(--grey);letter-spacing:.3px;white-space:nowrap}
  .contacts li{display:flex;align-items:center;height:17.5px}
  .contacts svg{width:12px;height:12px;margin-right:3px;flex:none}
  .contacts .social svg + svg{margin-left:4px;margin-right:6px}

  .band{position:absolute;left:0;right:0;bottom:0;height:18px;background:var(--teal-band)}
</style>
</head>
<body>

<section class="card card--front">
  <h1 class="wordmark"><span>Harbourline</span><span class="sub">Electrical Solutions</span></h1>
  <p class="services">ELECTRICAL CONSTRUCTION &amp; MAINTENANCE • LED LIGHTING &amp; AUTOMATION<br>• LIFE SAFETY SYSTEMS (FIRE ALARM / SECURITY) • DATA &amp; COMMUNICATION</p>
</section>

<section class="card card--back">
  <h2 class="wordmark"><span>Harbourline</span><span class="sub">Electrical Solutions</span></h2>
  <p class="sectors">COMMERCIAL<span class="sep">|</span>INDUSTRIAL<span class="sep">|</span>RESIDENTIAL</p>

  <div class="person">
    <p class="person__name">Marcus T. Hollings</p>
    <p class="person__role">Project Manager</p>
  </div>
  <div class="divider"></div>

  <ul class="contacts">
    <li>
      <svg viewBox="0 0 12 12" aria-hidden="true"><circle cx="6" cy="6" r="5.3" fill="none" stroke="#10576c" stroke-width="0.9"/><path d="M4 3.3l1 .1.4 1.3-.6.5a4 4 0 0 0 1.9 1.9l.5-.6 1.3.4.1 1-.7.6C5.6 8.3 3.7 6.4 3.5 4z" fill="#10576c"/></svg>
      (441) 555-0187
    </li>
    <li>
      <svg viewBox="0 0 12 12" aria-hidden="true"><circle cx="6" cy="6" r="5.3" fill="none" stroke="#10576c" stroke-width="0.9"/><rect x="3.3" y="4" width="5.4" height="4" fill="none" stroke="#10576c" stroke-width="0.8"/><path d="M3.3 4L6 6.2 8.7 4" fill="none" stroke="#10576c" stroke-width="0.8"/></svg>
      hlelectricalsolutions@mailvento.com
    </li>
    <li class="social">
      <svg viewBox="0 0 12 12" aria-hidden="true"><circle cx="6" cy="6" r="5.3" fill="none" stroke="#10576c" stroke-width="0.9"/></svg>
      <svg viewBox="0 0 12 12" aria-hidden="true"><circle cx="6" cy="6" r="5.3" fill="none" stroke="#10576c" stroke-width="0.9"/></svg>
      @hlelectricalsolutions
    </li>
  </ul>

  <div class="band"></div>
</section>

</body>
</html>
```